Brimlow Plumbing Solutions

This is for my new plumbing company, I have attached an example of what I’m going for but want it to look better.

Target Market(s)

Home owners, real estate, etc.

Industry/Entity Type

Plumbing

Font styles to use
Other font styles liked:
• As per my logo and other examples uploaded

Colors

Designer to choose colors to be used in the design.

Requirements
Must have
• Must include my logo provided and similar to my flyer I have attached but better

```html
<!DOCTYPE html>
<html lang="en">
<head>
<meta charset="UTF-8">
<title>Brimlow Plumbing Solutions – Flyer</title>
<link rel="stylesheet" href="https://fonts.googleapis.com/css2?family=Inter:wght@400;500;600;700;800&display=swap">
<style>
  :root {
    --backdrop: #a9c9e4;
    --paper: #ffffff;
    --navy: #1c3c6e;
    --navy-mid: #5a86b4;
    --sky: #63b0e0;
    --tile-light: #a9cbe6;
    --orange: #f36f21;
    --ink: #16243a;
    --ink-soft: #2b3648;
  }
  * { box-sizing: border-box; margin: 0; padding: 0; }
  html, body { width: 1200px; height: 1200px; overflow: hidden; }
  body {
    background: var(--backdrop);
    font-family: "Inter", Arial, sans-serif;
    color: var(--ink);
    position: relative;
  }
  .flyer {
    position: absolute;
    left: 268px; top: 72px;
    width: 664px; height: 1060px;
    background: var(--paper);
  }
  .brand {
    position: absolute; top: 50px; left: 0; width: 100%;
    text-align: center;
  }
  .brand-name {
    font-size: 40px; font-weight: 800; letter-spacing: 0.5px;
    color: var(--navy); line-height: 1;
  }
  .brand-sub {
    margin-top: 8px; font-size: 13px; font-weight: 600;
    letter-spacing: 0.3px; color: var(--navy);
  }
  .hero-shapes { position: absolute; left: 0; top: 158px; }
  .hero-text { position: absolute; left: 54px; top: 244px; color: #fff; }
  .hero-title { font-size: 37px; font-weight: 600; line-height: 44px; letter-spacing: -0.3px; }
  .hero-sub { margin-top: 18px; font-size: 23px; font-weight: 500; line-height: 35px; }
  .hero-sub mark {
    background: var(--sky); color: #fff; padding: 0 4px; border-radius: 3px;
  }
  .discount-badge {
    position: absolute; left: 512px; top: 327px;
    width: 110px; height: 110px; border-radius: 50%;
    background: var(--orange); color: #fff;
    display: flex; flex-direction: column; align-items: center; justify-content: center;
    font-size: 15px; font-weight: 600; line-height: 18px; text-align: center;
  }
  .discount-badge strong { font-size: 20px; font-weight: 800; line-height: 22px; }
  .services-title {
    position: absolute; left: 52px; top: 518px;
    font-size: 23px; font-weight: 600; color: var(--ink);
  }
  .service-grid {
    position: absolute; left: 50px; top: 563px;
    width: 563px;
    display: grid;
    grid-template-columns: 179px 185px 181px;
    grid-template-rows: 155px 162px;
    column-gap: 9px; row-gap: 9px;
  }
  .service-tile {
    display: flex; flex-direction: column; align-items: center; justify-content: center;
    text-align: center; font-size: 17px; font-weight: 500; line-height: 21px;
    padding: 0 10px;
  }
  .service-tile svg { width: 44px; height: 44px; margin-bottom: 12px; }
  .tile-light { background: var(--tile-light); color: var(--ink); }
  .tile-dark { background: var(--navy); color: #fff; }
  .tile-mid { background: var(--navy-mid); color: #fff; }
  .tagline {
    position: absolute; left: 54px; top: 935px;
    font-size: 15px; font-weight: 500; color: var(--ink-soft);
  }
  .contact-heading {
    position: absolute; left: 352px; top: 972px;
    font-size: 16px; font-weight: 600; color: var(--ink);
  }
  .contact-row {
    position: absolute; left: 54px; top: 996px;
    display: flex; align-items: center; gap: 20px;
    font-size: 14px; color: var(--ink-soft);
  }
  .contact-item { display: flex; align-items: center; gap: 7px; white-space: nowrap; }
  .contact-item svg { width: 19px; height: 19px; }
  .social-list { display: flex; gap: 8px; margin-left: 6px; }
  .social-dot { width: 21px; height: 21px; border-radius: 50%; background: var(--ink); }
</style>
</head>
<body>
  <main class="flyer">
    <header class="brand">
      <div class="brand-name">BRIMLOW</div>
      <div class="brand-sub">PLUMBING SOLUTIONS</div>
    </header>

    <svg class="hero-shapes" width="664" height="340" viewBox="0 0 664 340" aria-hidden="true">
      <path d="M232 8 Q234 0 244 0 H420 L414 28 H228 Z" fill="var(--sky)"/>
      <path d="M0 14 H478 Q500 14 494 36 L430 312 Q424 336 400 336 H0 Z" fill="var(--navy)"/>
      <path d="M480 14 H664 V336 H420 L472 32 Q476 14 490 14 Z" fill="var(--sky)" opacity="0.92"/>
    </svg>

    <section class="hero-text">
      <h1 class="hero-title">Your Local Reliable<br>Sydney Plumber</h1>
      <p class="hero-sub">Specialising in <mark>Plumbing,</mark><br>Drainage &amp; Gas Maintenance</p>
    </section>

    <div class="discount-badge"><strong>10% OFF</strong>FIRST JOB</div>

    <h2 class="services-title">Key Services</h2>

    <section class="service-grid">
      <div class="service-tile tile-light">
        <svg viewBox="0 0 44 44" fill="none" stroke="currentColor" stroke-width="1.8"><path d="M16 6h10M19 6v12l-8 14a5 5 0 0 0 5 7h10"/><path d="M30 24c0 0-4 5-4 8a4 4 0 0 0 8 0c0-3-4-8-4-8z"/></svg>
        Emergency<br>Plumbing
      </div>
      <div class="service-tile tile-light">
        <svg viewBox="0 0 44 44" fill="none" stroke="currentColor" stroke-width="1.8"><path d="M10 8h14v8H10zM24 12h8l4 8M14 16l-4 20h8l4-20"/></svg>
        Blocked<br>Drains
      </div>
      <div class="service-tile tile-dark">
        <svg viewBox="0 0 44 44" fill="none" stroke="currentColor" stroke-width="1.8"><path d="M8 8l28 28M36 8L8 36"/><circle cx="30" cy="14" r="4"/></svg>
        Gas Fitting
      </div>
      <div class="service-tile tile-dark">
        <svg viewBox="0 0 44 44" fill="none" stroke="currentColor" stroke-width="1.8"><rect x="8" y="8" width="28" height="26" rx="2"/><path d="M12 16h20M12 22h12M12 28h8"/></svg>
        Hot Water<br>Systems
      </div>
      <div class="service-tile tile-mid">
        <svg viewBox="0 0 44 44" fill="none" stroke="currentColor" stroke-width="1.8"><rect x="9" y="8" width="26" height="28" rx="2"/><path d="M15 26c3 4 11 4 14 0"/></svg>
        Leak<br>Detection
      </div>
      <div class="service-tile tile-light">
        <svg viewBox="0 0 44 44" fill="none" stroke="currentColor" stroke-width="1.8"><rect x="8" y="10" width="22" height="26" rx="2"/><path d="M12 18h14M12 24h14M12 30h8"/><circle cx="32" cy="12" r="6"/></svg>
        Bathroom<br>Repairs
      </div>
    </section>

    <p class="tagline">Reliable Plumbing. Real Solutions</p>
    <p class="contact-heading">Contact</p>

    <footer class="contact-row">
      <span class="contact-item">
        <svg viewBox="0 0 24 24" fill="var(--ink)"><path d="M6.6 10.8a15 15 0 0 0 6.6 6.6l2.2-2.2a1 1 0 0 1 1-.25 11 11 0 0 0 3.6.6 1 1 0 0 1 1 1V20a1 1 0 0 1-1 1A17 17 0 0 1 3 4a1 1 0 0 1 1-1h3.5a1 1 0 0 1 1 1c0 1.25.2 2.45.6 3.6a1 1 0 0 1-.25 1z"/></svg>
        02 9000 1234
      </span>
      <span class="contact-item">
        <svg viewBox="0 0 24 24" fill="none" stroke="var(--ink)" stroke-width="2"><rect x="3" y="5" width="18" height="14"/><path d="M3 5l9 8 9-8"/></svg>
        hello@brimlow.com.au
      </span>
      <span class="contact-item">
        <svg viewBox="0 0 24 24" fill="none" stroke="var(--ink)" stroke-width="1.6"><circle cx="12" cy="12" r="9"/><path d="M3 12h18M12 3c3 3 3 15 0 18M12 3c-3 3-3 15 0 18"/></svg>
        brimlow.com.au
      </span>
      <span class="social-list">
        <span class="social-dot"></span><span class="social-dot"></span><span class="social-dot"></span><span class="social-dot"></span>
      </span>
    </footer>
  </main>
</body>
</html>
```